Pitch Deck Redesign

We are a company in the ed-tech/gaming business wishing to fine-tune the looks of our pitch deck/company presentation.
Attached is the current template we use. And while we want to keep the headlines, general structure and the flow represented in various graphs, we want a design whizz to fine-tune the looks of it, updating graphics and add a bit more graphics. In the end we basically want to give the template a professional edge while still conveying the design philosophy we're trying to achieve, the philosophy is as follows:
A combination of education and playfulness/digital entertainment (particularly gaming). It should additionally be clean, not cluttered yet with a hint of fun.
We of course want to be able to simply ad our own texts as well as our to logo various elements

```html
<!DOCTYPE html>
<html lang="en">
<head>
<meta charset="utf-8">
<title>Lernix Pitch Deck</title>
<link rel="stylesheet" href="https://fonts.googleapis.com/css2?family=Arimo:wght@700&family=Lato:wght@400;700;900&display=swap">
<style>
:root{
  --stage:#7a7a7a;
  --white:#ffffff;
  --ink:#1a1a1a;
  --text:#2b2b2b;
  --blue:#0d72c1;
  --blue-deep:#0a63ad;
  --blue-light:#5b9bd8;
  --sky:#8aaabe;
  --green:#3d9a3a;
  --green-soft:#6aab44;
  --purple:#a433e0;
  --gold:#c9a01c;
  --orange:#ef7d2e;
  --yellow:#f5c518;
}
*{margin:0;padding:0;box-sizing:border-box}
html,body{width:1200px;height:1041px;overflow:hidden;background:var(--stage)}
.board{position:relative;width:1200px;height:1041px;background:var(--stage)}
.slide{position:absolute;width:502px;height:282px;background:var(--white);overflow:hidden;
  font-family:"Lato",sans-serif;color:var(--text);box-shadow:0 6px 16px rgba(0,0,0,.35)}
.s1{left:87px;top:74px;background:linear-gradient(120deg,#94b2c6,#7ea1b8)}
.s4{left:611px;top:74px}
.s2{left:87px;top:379px}
.s5{left:611px;top:379px}
.s3{left:87px;top:684px;background:linear-gradient(135deg,#0f6fbd,#1a7fd6)}
.s6{left:611px;top:684px}
.abs{position:absolute}
.heading{position:absolute;font-family:"Arimo",sans-serif;font-weight:700;font-size:20px;color:var(--ink);line-height:1.25;letter-spacing:.2px;z-index:1}
.heading .accent{color:var(--blue)}
.wordmark{position:absolute;font-family:"Lato",sans-serif;font-weight:900;color:var(--blue);letter-spacing:1.5px;line-height:1;z-index:1}
.body{position:absolute;font-size:9px;line-height:16.4px;color:var(--text);z-index:1}
.body p+p{margin-top:10px}
.stat-num{position:absolute;font-weight:700;line-height:1}
.stat-desc{position:absolute;font-size:13px;color:var(--ink)}
.inline-desc{font-size:10px;font-weight:400;color:var(--ink);margin-left:6px}
.badge{position:absolute;width:24px;height:24px;border-radius:50%;background:var(--blue-deep);color:var(--white);z-index:2;
  font-family:"Arimo",sans-serif;font-weight:700;font-size:11px;display:flex;align-items:center;justify-content:center}
.photo{position:absolute;z-index:0}
.tagline{position:absolute;left:30px;top:98px;font-size:20.5px;line-height:26px;color:#1f2a33;width:270px;z-index:1}
.label{position:absolute;font-weight:700;font-size:10px;color:var(--ink);transform:translateX(-50%)}
</style>
</head>
<body>
<div class="board">

  <section class="slide s1">
    <div class="photo" role="img" aria-label="Hand holding a smartphone showing the app menu" style="left:296px;top:74px;width:206px;height:208px;background:linear-gradient(160deg,#7d9fb6,#5d7f97 60%,#b8c1c8)"></div>
    <svg class="abs" style="left:0;top:0" width="502" height="282" aria-hidden="true">
      <polygon points="0,282 146,217 297,282" fill="var(--blue)"/>
    </svg>
    <div class="wordmark" style="left:30px;top:40px;font-size:40px">Lernix</div>
    <p class="tagline">Turning the billion dollar gaming industry into an education-encouraging tool</p>
    <div class="badge" style="left:465px;top:247px">01</div>
  </section>

  <section class="slide s4">
    <h2 class="heading" style="left:29px;top:17px">WHY WE EXIST</h2>
    <div class="wordmark" style="left:370px;top:19px;font-size:21px">Lernix</div>
    <div class="stat-num" style="left:30px;top:53px;font-size:18px;color:var(--blue)">2,8 billion<span class="inline-desc">Stat description</span></div>
    <div class="body" style="left:30px;top:83px;width:260px">
      <p>Lorem ipsum dolor sit amet, consectetur adipiscing elit, sed do eiusmod tempor incididunt ut labore et dolore magna aliqua. Quis ipsum suspendisse ultrices gravida.<br>Eget egestas purus viverra accumsan. Luctus accumsan tortor posuere acut consequat semper.</p>
    </div>
    <div class="stat-num" style="left:332px;top:54px;font-size:25px;color:var(--green)">9 of10</div>
    <div class="stat-desc" style="left:334px;top:85px">Stat description</div>
    <div class="stat-num" style="left:332px;top:116px;font-size:25px;color:var(--purple)">90%</div>
    <div class="stat-desc" style="left:334px;top:147px">Stat description</div>
    <div class="photo" role="img" aria-label="Gamer wearing a headset in neon light" style="left:0;top:177px;width:254px;height:105px;background:linear-gradient(120deg,#3a1a5a,#6a2a8a 35%,#1f5a4a 70%,#2a3a3a)"></div>
    <div class="photo" role="img" aria-label="Fantasy game landscape with glowing portal" style="left:257px;top:177px;width:159px;height:105px;background:linear-gradient(180deg,#2a2a7a,#4a4ac0 55%,#1a2a5a)"></div>
    <div class="photo" role="img" aria-label="Child playing with a game controller in colourful light" style="left:419px;top:177px;width:83px;height:55px;background:linear-gradient(120deg,#c0306a,#4a3aa0)"></div>
    <div class="badge" style="left:471px;top:256px">04</div>
  </section>

  <section class="slide s2">
    <svg class="abs" style="left:0;top:0" width="502" height="282" aria-hidden="true">
      <polyline points="410,-4 410,37 469,4" fill="none" stroke="var(--green-soft)" stroke-width="3"/>
      <circle cx="506" cy="44" r="26" fill="var(--blue-light)"/>
      <rect x="462" y="97" width="5" height="22" rx="2.5" fill="var(--yellow)"/>
      <rect x="462" y="141" width="5" height="22" rx="2.5" fill="var(--yellow)"/>
      <circle cx="427" cy="141" r="17" fill="none" stroke="var(--blue-light)" stroke-width="5"/>
      <polyline points="506,195 466,195 466,250 506,250" fill="none" stroke="var(--green-soft)" stroke-width="3"/>
      <circle cx="429" cy="273" r="24" fill="var(--orange)"/>
    </svg>
    <svg class="abs" style="left:0;top:0" width="502" height="282" role="img" aria-label="Gaming headset and controllers in blue light">
      <defs><linearGradient id="gDesk" x1="0" y1="0" x2="1" y2="1"><stop offset="0" stop-color="#1d7fd0"/><stop offset="1" stop-color="#0b4f8f"/></linearGradient></defs>
      <polygon points="0,282 146,206 299,282" fill="url(#gDesk)"/>
    </svg>
    <h2 class="heading" style="left:30px;top:20px">MISSION STATEMENT<br><span class="accent">AND VISION</span></h2>
    <div class="wordmark" style="left:290px;top:20px;font-size:21px">Lernix</div>
    <div class="body" style="left:30px;top:81px;width:344px;font-size:9.7px;line-height:19.7px;text-align:justify">
      Lorem ipsum dolor sit amet, consectetur adipiscing elit, sed do eiusmod tempor incididunt ut labore et dolore magna aliqua. Quis ipsum suspendisse ultrices gravida. Risus commodo viverra maecenas accumsan lacus vel facilisis. Lorem ipsum dolor sit amet, consectetur adipiscing elit, sed do eiusmodncididunt ut labore et dolore magna aliquis ipsum suspendisse ultrices gravida.isus commodo viverra maecenas accumsan lacus vel facilisis.
    </div>
    <div class="badge" style="left:471px;top:256px">02</div>
  </section>

  <section class="slide s5">
    <svg class="abs" style="left:0;top:0" width="502" height="282" aria-hidden="true">
      <polyline points="411,-4 411,37 470,4" fill="none" stroke="var(--blue)" stroke-width="3"/>
      <circle cx="506" cy="44" r="26" fill="var(--blue)"/>
      <rect x="465" y="97" width="5" height="22" rx="2.5" fill="var(--blue)"/>
      <rect x="465" y="141" width="5" height="22" rx="2.5" fill="var(--blue)"/>
      <circle cx="428" cy="141" r="17" fill="none" stroke="var(--blue)" stroke-width="5"/>
      <polyline points="506,195 468,195 468,250 506,250" fill="none" stroke="var(--blue)" stroke-width="3"/>
      <circle cx="429" cy="279" r="25" fill="var(--blue)"/>
    </svg>
    <h2 class="heading" style="left:29px;top:17px">WHY WE EXIST</h2>
    <div class="stat-num" style="left:30px;top:53px;font-size:18px;color:var(--blue)">15,7%<span class="inline-desc">Stat description</span></div>
    <div class="body" style="left:30px;top:85px;width:256px;font-size:9px;line-height:13px">
      <p>Lorem ipsum dolor sit amet, consectetur adipiscing elit, sed do eiusmod tempor incididunt ut labore et dolore magna aliqua. Quis ipsum suspendisse ultrices gravida.</p>
      <p style="margin-top:13px">Eget egestas purus viverra accumsan. Luctus accumsan tortor posuere acut consequat semper.</p>
      <p style="margin-top:13px">Convallis convallis tellus id interdum velit laoreet. Egestas quis ipsum suspendisse ultrices.</p>
    </div>
    <div class="stat-num" style="left:325px;top:37px;font-size:24px;color:var(--green)">43%</div>
    <div class="stat-desc" style="left:327px;top:68px">Stat description</div>
    <div class="stat-num" style="left:329px;top:161px;font-size:24px;color:var(--purple)">1of 5</div>
    <div class="stat-desc" style="left:331px;top:192px">Stat description</div>
    <div class="stat-num" style="left:31px;top:220px;font-size:24px;color:var(--gold)">30%</div>
    <div class="stat-desc" style="left:33px;top:251px">Stat description</div>
    <div class="wordmark" style="left:200px;top:240px;font-size:21px">Lernix</div>
    <div class="badge" style="left:471px;top:256px">05</div>
  </section>

  <section class="slide s3">
    <div class="photo" role="img" aria-label="Game controllers with neon triangle shapes" style="left:210px;top:150px;width:292px;height:132px;background:radial-gradient(ellipse at 65% 60%,#3fb0f0,#1a7fd6 70%,rgba(26,127,214,0))"></div>
    <h2 class="heading" style="left:30px;top:18px;color:var(--white)">STORY</h2>
    <div class="body" style="left:30px;top:54px;width:440px;font-size:10px;line-height:19.7px;color:var(--white)">
      Lorem ipsum dolor sit amet, consectetur adipiscing elit, sed do eiusmod tempor incididunt ut labore et dolore magna aliqua. Quis ipsum suspendisse ultrices gravida. Risus commodo viverra maecenas accumsan lacus vel facilisis. Lorem ipsum dolor sit amet, consectetur adipiscing eiusmodncididunt ut labore et dolore magna aliquis ipsum suspendisse ultrices gravida.isus commodo viverra maecenas accumsan lacus vel facilisis. Lorem ipsum dolor sit amet, consectetur adipiscing elit, sed do eiusmod tempor incididunt ut labore et dolore magna aliqua. Quis ipsum suspendisse ultrices gravida. Risus commodo viverra maecenas accumsan lacus vel facilisis.
    </div>
    <div class="wordmark" style="left:30px;top:238px;font-size:21px;color:var(--white)">Lernix</div>
    <div class="badge" style="left:471px;top:256px">03</div>
  </section>

  <section class="slide s6">
    <svg class="abs" style="left:0;top:0" width="502" height="282" aria-hidden="true">
      <g opacity=".12">
        <circle cx="506" cy="44" r="26" fill="var(--blue-light)"/>
        <circle cx="430" cy="141" r="17" fill="none" stroke="var(--blue-light)" stroke-width="4"/>
        <polyline points="506,195 468,195 468,250 506,250" fill="none" stroke="var(--green-soft)" stroke-width="3"/>
        <circle cx="430" cy="279" r="25" fill="var(--orange)"/>
      </g>
      <line x1="90" y1="216" x2="370" y2="216" stroke="var(--blue)" stroke-width="2"/>
      <polygon points="31,216 47,189 79,189 95,216 79,243 47,243" fill="var(--blue)"/>
      <circle cx="63" cy="216" r="11" fill="none" stroke="var(--white)" stroke-width="2"/>
      <polygon points="163,216 186,190 277,190 300,216 277,242 186,242" fill="var(--white)" stroke="var(--blue)" stroke-width="2.5"/>
      <polygon points="368,216 384,189 416,189 432,216 416,243 384,243" fill="var(--blue)"/>
      <circle cx="400" cy="216" r="11" fill="none" stroke="var(--white)" stroke-width="2"/>
    </svg>
    <h2 class="heading" style="left:32px;top:17px">OUR SOLUTION</h2>
    <div class="wordmark" style="left:382px;top:19px;font-size:21px">Lernix</div>
    <div class="body" style="left:30px;top:60px;width:440px;font-size:9.3px;line-height:13px">
      <p>Lorem ipsum dolor sit amet, consectetur adipiscing elit, sed do eiusmod tempor incididunt ut labore et dolore magna aliqua. Pharetra sitamet aliquam id diam maecenas ultricies. Volutpat maecenas volutpat</p>
      <p style="margin-top:13px">Eget egestas purus viverra accumsan. Luctus accumsan tortor posuere ac ut consequat semper. Odio morbi quis commodo odio. Viverra justonec ultrices dui sapien.</p>
      <p style="margin-top:13px">Convallis convallis tellus id interdum velit laoreet. Egestas quis ipsumsuspendisse ultrices. Dictumst quisque sagittis purus sit amet volutpatconsequat. Mauris augue neque gravida</p>
    </div>
    <div class="wordmark" style="left:186px;top:205px;width:91px;text-align:center;font-size:20px">Lernix</div>
    <div class="label" style="left:63px;top:252px">Description</div>
    <div class="label" style="left:231px;top:252px">Graphic</div>
    <div class="label" style="left:400px;top:252px">Description</div>
    <div class="badge" style="left:471px;top:256px">06</div>
  </section>

</div>
</body>
</html>
```